New Business Card for Software Company

We are looking at rebranding a 10 year old company that specializes in PDF and DWF solutions for Architects and Engineers. We will attach the new company logo that we are going with so you can work with that and complimentary colors.
The sample information we would like on the business card is:
Gerald Pinfold
Vice President
4738 W. Harrowgate Lane. STE 305
PMB#417
Mesa, AZ 85374
866-392-5074 US Toll Free
123-456-3190 Cell
gpinfold@plavorix.com
The old tag line that we had on the business cars was.
Delivering Dependable Document Tools for Drawing Files Across the Worldwide Design Trade.
If you have an idea for a better tag line we are open to that also.
Updates
We would like to thank all of the Designers for their wonderful work. We apologize that we will not have the time to provide feedback to everyone. There is just so many innovative and professional designs that you have all created making our decision even harder.
Target Market(s)
Architects and Engineers
Industry/Entity Type
Business
Look and feel

```html
<!DOCTYPE html>
<html lang="en">
<head>
<meta charset="utf-8">
<title>Plavorix Business Card</title>
<link rel="stylesheet" href="https://fonts.googleapis.com/css2?family=Source+Sans+3:wght@400;600;700&display=swap">
<style>
  :root {
    --canvas: #ecebe8;
    --card-white: #ffffff;
    --card-grey: #6d6d6f;
    --orange: #f26a1b;
    --ink: #4d4d4f;
    --ink-soft: #6f6f72;
    --divider: #c9c9c9;
    --on-dark: #f2f2f2;
  }
  * { box-sizing: border-box; margin: 0; padding: 0; }
  html, body { width: 1200px; height: 720px; overflow: hidden; }
  body {
    background: var(--canvas);
    font-family: "Source Sans 3", "Myriad Pro", Arial, sans-serif;
    color: var(--ink);
  }
  .sheet {
    position: relative;
    width: 1200px;
    height: 720px;
    display: flex;
    align-items: center;
    justify-content: center;
    gap: 40px;
  }
  .card {
    position: relative;
    width: 540px;
    height: 309px;
    box-shadow: 0 2px 10px rgba(0,0,0,0.18);
    overflow: hidden;
  }

  /* Front */
  .card--front { background: var(--card-white); }
  .brand {
    position: absolute;
    top: 48px;
    left: 0;
    right: 0;
    display: flex;
    align-items: center;
    justify-content: center;
    gap: 14px;
  }
  .brand__dot {
    width: 50px;
    height: 50px;
    border-radius: 50%;
    background: var(--orange);
  }
  .brand__name {
    font-size: 56px;
    font-weight: 700;
    line-height: 1;
    letter-spacing: -1px;
    color: var(--ink);
  }
  .details {
    position: absolute;
    top: 152px;
    left: 0;
    right: 0;
    display: flex;
    justify-content: center;
  }
  .person {
    text-align: right;
    padding-right: 16px;
    border-right: 1px solid var(--divider);
    font-size: 14px;
    line-height: 1.3;
  }
  .person__name {
    font-size: 19px;
    font-weight: 700;
    color: var(--orange);
    line-height: 1.1;
  }
  .person__title {
    color: var(--ink-soft);
    margin-bottom: 10px;
  }
  .person__address { color: var(--ink); }
  .contact {
    list-style: none;
    padding-left: 14px;
    font-size: 14px;
    line-height: 1.2;
  }
  .contact__item {
    display: flex;
    align-items: center;
    gap: 7px;
    margin-bottom: 9px;
  }
  .contact__icon { width: 12px; height: 12px; flex: none; }

  /* Back */
  .card--back { background: var(--card-grey); }
  .back-brand {
    position: absolute;
    top: 70px;
    left: 0;
    right: 0;
    display: flex;
    align-items: center;
    justify-content: center;
    gap: 16px;
  }
  .back-brand__dot {
    width: 76px;
    height: 76px;
    border-radius: 50%;
    background: var(--orange);
  }
  .back-brand__name {
    font-size: 58px;
    font-weight: 700;
    letter-spacing: -1px;
    color: var(--on-dark);
  }
  .tagline {
    position: absolute;
    left: 0;
    right: 0;
    bottom: 46px;
    text-align: center;
    font-size: 19px;
    line-height: 1.3;
    color: var(--on-dark);
  }
</style>
</head>
<body>
  <main class="sheet">
    <section class="card card--front" aria-label="Business card front">
      <div class="brand">
        <span class="brand__dot"></span>
        <span class="brand__name">Plavorix</span>
      </div>
      <div class="details">
        <div class="person">
          <p class="person__name">Gerald Pinfold</p>
          <p class="person__title">Vice President</p>
          <p class="person__address">4738 W. Harrowgate Lane. STE 305<br>PMB#417, Mesa, AZ 85374</p>
        </div>
        <ul class="contact">
          <li class="contact__item">
            <svg class="contact__icon" viewBox="0 0 12 12" aria-hidden="true">
              <circle cx="6" cy="6" r="5.5" fill="none" stroke="#f26a1b" stroke-width="1"/>
              <path d="M4 3.2 L5.2 3 L5.6 4.6 L4.9 5.2 Q5.5 6.6 6.8 7.1 L7.4 6.4 L9 6.8 L8.8 8 Q6.5 8.6 4.8 7 Q3.4 5.4 4 3.2 Z" fill="#f26a1b"/>
            </svg>
            <span>866-392-5074US(TF)</span>
          </li>
          <li class="contact__item">
            <svg class="contact__icon" viewBox="0 0 12 12" aria-hidden="true">
              <rect x="3" y="0.5" width="6" height="11" rx="1.2" fill="#f26a1b"/>
              <rect x="4" y="2" width="4" height="5" fill="#ffffff"/>
              <circle cx="6" cy="9.3" r="0.8" fill="#ffffff"/>
            </svg>
            <span>123-456-3190</span>
          </li>
          <li class="contact__item">
            <svg class="contact__icon" viewBox="0 0 12 12" aria-hidden="true">
              <rect x="0.5" y="2.5" width="11" height="7.5" rx="1" fill="#f26a1b"/>
              <path d="M1 3 L6 7 L11 3" fill="none" stroke="#ffffff" stroke-width="1"/>
            </svg>
            <span>gpinfold@plavorix.com</span>
          </li>
        </ul>
      </div>
    </section>

    <section class="card card--back" aria-label="Business card back">
      <div class="back-brand">
        <span class="back-brand__dot"></span>
        <span class="back-brand__name">Plavorix</span>
      </div>
      <p class="tagline">Delivering Dependable Document Tools for<br>Drawing Files Across the Worldwide Design Trade</p>
    </section>
  </main>
</body>
</html>
```